Real Estate - Property Management Prospectus/Brochure

We need a prospectus made up, around 9-10 pages including the cover page pages 3 onwards can be all a similar template happy for the front cover to have lots of black. I would like it to look very classy and futuristic, high end, blacks, silvers and whites, i am specializing in managing high end rental properties. i would like to design to correspond with the logo. I need to be able to email this booklet mostly - and also be able to print and mail out as well. I would like it crisp and clean as well - not to much on a page. Please note - happy for the cover to be simple with the logo added - prefer lots of black and with the other pages - they can all be a similar layout template to make this job easier? My website is www.leasemeridian.com.au and phone is 0418 293 547 email is tmarsh@leasemeridian.com.au
Target Market(s)
Investors
Industry/Entity Type
Real Estate
Requirements
Should not have
- Bright greens or bold colours

```html
<!DOCTYPE html>
<html lang="en">
<head>
<meta charset="utf-8">
<title>Lease Meridian – Introduction</title>
<link rel="stylesheet" href="https://fonts.googleapis.com/css2?family=Fira+Sans+Condensed:wght@400&family=Fira+Sans+Extra+Condensed:wght@300;400&display=swap">
<style>
  :root {
    --page-top: #e6e6e6;
    --page-bottom: #ffffff;
    --ink: #1c1c1c;
    --ink-soft: #3a3a3a;
    --brand-grey: #5c5c5c;
    --photo-sky: #f4f5f5;
    --photo-mid: #b7babb;
    --photo-low: #8d918b;
    --photo-sea: #6fa7a3;
  }
  * { box-sizing: border-box; margin: 0; padding: 0; }
  html, body { width: 848px; height: 1200px; overflow: hidden; }
  body { background: var(--page-bottom); }

  .page {
    position: relative;
    width: 848px;
    height: 1200px;
    overflow: hidden;
    background: linear-gradient(to bottom, var(--page-top) 0%, #f3f3f3 35%, var(--page-bottom) 60%);
    color: var(--ink);
  }

  .brand {
    position: absolute;
    top: 42px;
    right: 26px;
    display: flex;
    align-items: center;
    gap: 10px;
    font-family: "Fira Sans Condensed", sans-serif;
    font-weight: 400;
    font-size: 21px;
    letter-spacing: 5px;
    color: var(--brand-grey);
  }
  .brand-mark {
    width: 14px;
    height: 14px;
    background: var(--brand-grey);
  }

  .page-title {
    position: absolute;
    top: 138px;
    left: 97px;
    font-family: "Fira Sans Extra Condensed", sans-serif;
    font-weight: 300;
    font-size: 50px;
    line-height: 1;
    color: var(--ink);
  }

  .intro {
    position: absolute;
    top: 372px;
    left: 97px;
    width: 655px;
    font-family: "Fira Sans Condensed", sans-serif;
    font-weight: 400;
    font-size: 18px;
    line-height: 31px;
    text-align: justify;
    color: var(--ink-soft);
  }
  .intro p + p { margin-top: 16px; }

  .skyline-photo {
    position: absolute;
    left: 0;
    bottom: 0;
    width: 848px;
    height: 520px;
    background:
      linear-gradient(100deg, transparent 62%, rgba(111,167,163,0.55) 85%, var(--photo-sea) 100%),
      linear-gradient(to bottom, rgba(255,255,255,0) 0%, var(--photo-sky) 30%, var(--photo-mid) 62%, var(--photo-low) 100%);
  }
</style>
</head>
<body>
  <main class="page">
    <div class="brand">
      <span class="brand-mark"></span>
      <span class="brand-name">LEASE MERIDIAN</span>
    </div>

    <h1 class="page-title">Introduction</h1>

    <section class="intro">
      <p>Lease Meridian was founded on the belief that investment property management should deliver results that go beyond our client’s expectations.</p>
      <p>Lease Meridian is building a reputation by excelling in every aspect of the property management process, bringing innovation, confidence, and creativeness with an unparalleled commitment to excellence, these values echo in all aspects of Lease Meridian.</p>
    </section>

    <div class="skyline-photo" role="img" aria-label="Aerial photograph of a coastal city skyline with high-rise towers, a sandy beach and turquoise ocean surf"></div>
  </main>
</body>
</html>
```